Letterhead Design for Law Firm

**Edit: I have added the photo of a bottom that I like.

------
We are looking for a re-design of our new letterhead. The letterhead is for a law firm and will be used for digital and traditionally printed correspondence.

Here are some suggestions:

- Please use colours are #8ec900 and simple black.
- Please do not use any type of "waves" at the bottom of the page. This is not in style at all.
- Please stay modern yet conservative.
- Please use font Segoe UI Light or similar if you can
- Avoid clipart or illustrations.
- Utilize ample white space in the layout so the design looks clean and information is easy to read at a glance. Don't overcrowd the letterhead.
- Make sure the letterhead design is consistent with our brand identity (see corvelith.ca)
-Please, no black headers or footers.

I am attaching my current letterhead and signature for your convenience.

Remember, the letterhead is an extension of our professional identity. We are a successful firm and trial lawyers who correspond with insurers, judges, lawyers, courts, clients, etc. Make it new, modern, attractive, yet powerful and conservative.

It needs to be easily printable. I would like the bleed removed in print so the black bar the bottom crosses the page (but the text is not near the edges)
Updates

Low design quality

Target Market(s)

Clients, Government Offices, Judiciary, Lawyers, Insurance Companies, Colleagues.

Industry/Entity Type

Law

Other font styles liked:
• Segoe UI LIght, Calibri Light,

Colors
00AB8E
00BBA5
67D7C9
C6EFE9
E9F9F6

Requirements
Must have
• Everything that is on the letterhead now.
Nice to have
• Cutting Edge design, yet conservative.
Should not have
• law firm cliche design, images,

```html
<!DOCTYPE html>
<html lang="en">
<head>
<meta charset="utf-8">
<title>Vardell Personal Injury Lawyers – Letterhead</title>
<link rel="stylesheet" href="https://fonts.googleapis.com/css2?family=Open+Sans:wght@300;400;600;700&display=swap">
<style>
  :root {
    --brand-green: #8ec900;
    --brand-black: #000000;
    --fold-grey: #4a4a4a;
    --paper: #f9f8f9;
    --ink: #1d1d1d;
    --backdrop: #e6e6e6;
    --sig-tone: #c9c9c9;
  }
  * { margin: 0; padding: 0; box-sizing: border-box; }
  html, body { width: 1200px; height: 1111px; overflow: hidden; }
  body { background: var(--backdrop); font-family: "Open Sans", sans-serif; color: var(--ink); position: relative; }

  .letterhead {
    position: absolute; left: 196px; top: 35px;
    width: 1224px; height: 1578px;
    background: var(--paper);
    transform: scale(0.66); transform-origin: top left;
    box-shadow: 0 4px 18px rgba(0,0,0,0.18);
  }
  .band { position: absolute; left: 0; width: 1224px; display: block; }
  .band--header { top: 0; height: 156px; }
  .band--footer { top: 1484px; height: 66px; }

  .firm-name {
    position: absolute; left: 92px; top: 24px; width: 368px;
    color: #ffffff; font-weight: 400; text-align: center; line-height: 1;
  }
  .firm-name__main { display: block; font-size: 78px; letter-spacing: 2px; }
  .firm-name__sub { display: block; font-size: 19px; letter-spacing: 2.4px; margin-top: 12px; }

  .contact-panel {
    position: absolute; left: 904px; top: 132px; height: 308px;
    border-left: 4px solid var(--brand-green);
    padding-left: 14px; padding-top: 0;
    font-size: 16.5px; line-height: 23px; font-weight: 400; margin-top: -10px;
  }
  .contact-panel b { font-weight: 700; }
  .contact-panel .web-accent { color: var(--brand-green); font-weight: 700; }
  .contact-panel .gap { height: 23px; }

  .letter-body {
    position: absolute; left: 85px; top: 284px; width: 970px;
    font-size: 20px; line-height: 27.5px; font-weight: 400; letter-spacing: 0.3px;
  }
  .letter-body .line { height: 27.5px; white-space: nowrap; }
  .letter-body .strong { font-weight: 600; letter-spacing: 0; }
  .re-row { display: flex; }
  .re-row__label { width: 297px; font-weight: 600; }
  .re-row__detail { font-weight: 600; letter-spacing: 0; }
  .re-rule { position: absolute; left: 82px; top: 808px; width: 970px; border-top: 1.5px solid var(--ink); }

  .sign-off {
    position: absolute; left: 85px; top: 1139px;
    font-size: 20px; line-height: 27px; letter-spacing: 0.3px;
  }
  .sign-off .firm-caps { font-weight: 600; letter-spacing: 0; }
  .signature-area {
    position: absolute; left: 85px; top: 1222px; width: 285px; height: 58px;
    background: linear-gradient(90deg, var(--sig-tone), rgba(201,201,201,0.35));
    border-radius: 4px;
  }
  .signatory {
    position: absolute; left: 85px; top: 1284px;
    font-size: 20px; line-height: 27px; letter-spacing: 0.3px;
  }
  .signatory__meta { font-size: 16.5px; line-height: 23.5px; }
  .signatory__meta .corp { font-weight: 600; }
</style>
</head>
<body>
  <main class="letterhead">
    <svg class="band band--header" viewBox="0 0 1224 156" aria-hidden="true">
      <polygon points="0,0 886,0 771,108 824,156 0,156" fill="var(--brand-green)"/>
      <polygon points="886,0 1224,0 1224,108 771,108" fill="var(--brand-black)"/>
      <polygon points="771,108 873,108 824,156" fill="var(--fold-grey)"/>
    </svg>

    <div class="firm-name">
      <span class="firm-name__main">VARDELL</span>
      <span class="firm-name__sub">PERSONAL INJURY LAWYERS</span>
    </div>

    <aside class="contact-panel">
      <div>www.<span class="web-accent">CORVELITH</span>.ca</div>
      <div>48 Harbour Street E., Suite 902</div>
      <div>Ashford, ON&nbsp; K7R 2B9</div>
      <div><b>T:</b> 905-555-0142</div>
      <div><b>F:</b> 905-555-0187</div>
      <div><b>File Clerk:</b> Nadia Ferrante</div>
      <div><b>Email:</b> nadia@corvelith.ca</div>
      <div class="gap"></div>
      <div><b>Practice Restricted</b></div>
      <div>Serious Personal Injury</div>
      <div>Wrongful Death Litigation</div>
      <div>Long-Term Disability Litigation</div>
      <div>Wrongful Dismissal Litigation</div>
      <div>Employee Terminations</div>
    </aside>

    <section class="letter-body">
      <div class="line strong">Without Prejudice</div>
      <div class="line"></div>
      <div class="line">March 13, 2024</div>
      <div class="line"></div>
      <div class="line strong">By Email</div>
      <div class="line"></div>
      <div class="line">Northvale Insurance Company</div>
      <div class="line">Claims Litigation Department</div>
      <div class="line">240 Ridgeline Road North</div>
      <div class="line">P.O. Box 4100</div>
      <div class="line">Elmbrook, ON&nbsp;&nbsp; N3K 5T2</div>
      <div class="line"></div>
      <div class="line">Attention:&nbsp; Mr. Dorian Kell</div>
      <div class="line"></div>
      <div class="line">Mr. Kell:</div>
      <div class="line"></div>
      <div class="re-row">
        <div class="re-row__label">Re:</div>
        <div class="re-row__detail">
          <div class="line">Halvorsen v. Deluca et al.</div>
          <div class="line">DOL:&nbsp; September 12, 2019</div>
          <div class="line">Pre-Mediation Settlement Proposal – March 13<sup>th</sup>, 2024</div>
        </div>
      </div>
    </section>
    <div class="re-rule"></div>

    <div class="sign-off">
      <div>Yours very truly,</div>
      <div class="firm-caps">VARDELL PERSONAL INJURY LAWYERS</div>
    </div>
    <div class="signature-area" role="img" aria-label="Handwritten signature of Evan T. Vardell"></div>
    <div class="signatory">
      <div>Evan T. Vardell</div>
      <div class="signatory__meta">
        <div class="corp">Vardell Law Professional Corporation</div>
        <div>/nf</div>
        <div>Encl.</div>
      </div>
    </div>

    <svg class="band band--footer" viewBox="0 0 1224 66" aria-hidden="true">
      <polygon points="0,0 943,0 893,66 0,66" fill="var(--brand-green)"/>
      <polygon points="955,0 1224,0 1224,66 911,66" fill="var(--brand-black)"/>
    </svg>
  </main>
</body>
</html>
```